Modern, clean and professional Wordpress design for a safety training company!

We are currently in the process of creating a new website for our business. We have hired a website developer and the main structure of our new Wordpress site is complete. We now need an overall design plan for the site. We need a very clean, professional and easy to follow website. Most of our website visitors only spend about 30-45 secs on our sites "shopping " so it is imperative that we have a strong Home Page.
Our company specializes in CPR and First Aid Certification Classes to businesses and individuals throughout Northern California. We provide these certifications two ways: ONSITE-We come to you, and HOSTED-we offer weekly classes at our 2 locations.
Our design needs to use the general green and blue colors of our logo. But we also like white.
The final design MUST communicate a legitimate, trustworthy and professional business. Our industry is VERY competitive and we need to STAND OUT.
Currently, the NEW website that we need a new design for is www.LifelineDrillWorks.com
Our old website is www.RescuePrepValleyHub.com and we really do like the design of this website, but we just needed a Wordpress site for SEO purposes.
These are 3 websites that we really:
http://morvaliontech.com/
http://www.tralbex.com/
https://www.plivant.com/
I have attached our Logo and other images if you need to use them but looking at the current two sites will be you best help.
Target Market(s)
1) Large businesses and industries that are looking for a company to provide ONSITE safety training classes at their office or place of work.
2) Individuals that need certifications for their jobs and other needs. These individuals are looking for a legitimate, trustworthy and professional environment to complete their training class.

```html
<!DOCTYPE html>
<html lang="en">
<head>
<meta charset="utf-8">
<title>Meridian Rescue Academy</title>
<link rel="stylesheet" href="https://fonts.googleapis.com/css2?family=Open+Sans:ital,wght@0,400;0,600;0,700;1,400&display=swap">
<style>
:root{
  --blue:#1b4a93;
  --blue-dark:#163d7c;
  --navy:#143a7a;
  --navy-deep:#0f2f66;
  --green:#7ea313;
  --green-dark:#6a8c0c;
  --red:#f04a37;
  --ink:#222;
  --text:#555;
  --muted:#777;
  --grey:#e4e4e4;
  --dark:#222326;
  --line:#e2e2e2;
  --white:#fff;
}
*{margin:0;padding:0;box-sizing:border-box}
html,body{width:727px;height:1200px;overflow:hidden}
body{position:relative;background:var(--white);font-family:"Open Sans",Arial,sans-serif;color:var(--text)}
.abs{position:absolute}

/* header */
.site-header{left:0;top:0;width:727px;height:61px;border-bottom:2px solid var(--blue)}
.brand{left:60px;top:14px;display:flex;align-items:center;gap:6px}
.brand-mark{width:16px;height:16px;border-radius:50%;background:var(--green)}
.brand-name{font-size:12px;font-weight:700;color:var(--blue);line-height:1.15}
.contact-bar{right:60px;top:12px;display:flex;gap:20px;font-size:7.5px;color:var(--blue);align-items:center}
.contact-item{display:flex;align-items:center;gap:6px}
.contact-icon{width:19px;height:19px;border-radius:50%;background:#2a8fd0;display:flex;align-items:center;justify-content:center}
.main-nav{right:60px;top:41px;display:flex;gap:35px;font-size:7.5px;color:#444}

/* hero */
.hero{left:0;top:61px;width:727px;height:320px;background:linear-gradient(120deg,#e6d7c6 0%,#d9a070 22%,#3a6fc6 40%,#f2f0ec 58%,#c9a47a 80%,#efe6d8 100%)}
.hero-title{left:60px;top:233px;color:var(--white);font-size:16px;font-weight:700;text-shadow:0 1px 3px rgba(0,0,0,.4)}
.hero-sub{left:60px;top:254px;color:var(--white);font-size:16px;text-shadow:0 1px 3px rgba(0,0,0,.4)}
.hero-arrows{left:64px;top:283px;display:flex;gap:3px}
.hero-arrow{width:11px;height:11px;border-radius:50%;background:rgba(255,255,255,.8)}
.hero-curve{left:0;top:350px;width:727px;height:40px}

/* feature cards */
.feature{width:143px;top:358px;background:var(--white);padding:6px 7px 0;box-shadow:0 0 4px rgba(0,0,0,.12)}
.feature-photo{height:82px}
.feature-label{height:21px;background:var(--blue);color:var(--white);font-size:7px;font-weight:700;padding:6px 10px 0}
.feature-body{top:476px;width:130px}
.feature-body h3{font-size:6.5px;font-weight:700;color:#333;margin-bottom:5px}
.feature-body p{font-size:6.3px;line-height:13px;color:var(--text)}

/* welcome */
.welcome-title{left:0;top:566px;width:727px;text-align:center;font-size:11px;font-weight:700;color:var(--blue)}
.welcome-text{left:84px;top:591px;width:560px;text-align:center;font-size:7.6px;line-height:15px;color:var(--muted)}

/* register */
.register{top:639px;height:66px;color:var(--white);padding:13px 0 0 18px}
.register h2{font-size:10px;font-weight:700;letter-spacing:.4px;margin-bottom:7px}
.register p{font-size:5.5px;line-height:12px;width:205px}
.register-tab{position:absolute;right:0;top:0;width:39px;height:66px;display:flex;align-items:center;justify-content:center}
.register-tab span{transform:rotate(-90deg);font-size:7.5px;font-weight:700;letter-spacing:.6px}
.register-online{left:84px;width:273px;background:var(--blue)}
.register-online .register-tab{background:var(--blue-dark)}
.register-later{left:370px;width:273px;background:var(--green)}
.register-later .register-tab{background:var(--green-dark)}

/* pricing */
.pricing{left:0;top:740px;width:727px;height:263px;background:var(--grey);border-top:1px solid #d5d5d5}
.pricing-kicker{left:60px;top:789px;font-size:11.5px;color:#333}
.pricing-title{left:60px;top:802px;font-size:15px;font-weight:700;color:var(--blue);letter-spacing:.5px}
.pricing-text{left:60px;top:828px;width:150px;font-size:6.3px;line-height:13.5px;color:var(--muted)}
.plan{top:778px;width:104px;height:192px;background:var(--white);border:1px solid #d8d8d8;text-align:center}
.plan-name{height:32px;background:var(--dark);color:var(--white);font-size:13px;font-weight:700;line-height:32px}
.plan-price{height:46px;background:#1c1d20;color:var(--white);border-top:1px solid #333;padding-top:7px}
.plan-price b{display:block;font-size:17px;font-weight:400;line-height:20px}
.plan-price span{display:block;font-size:8.5px;line-height:11px}
.plan-row{height:21px;font-size:6.3px;color:#333;line-height:21px;border-bottom:1px solid var(--line)}
.plan-row.alt{background:#f4f4f4}
.plan-btn{margin:9px auto 0;width:93px;height:21px;background:#111;color:var(--white);font-size:8.5px;font-weight:600;line-height:21px;border-radius:2px}
.plan-featured{top:772px;width:114px;height:203px;box-shadow:0 0 6px rgba(0,0,0,.15)}
.plan-featured .plan-name{height:38px;line-height:40px}
.plan-featured .plan-name,.plan-featured .plan-price{background:var(--red);border-top-color:#e2402e}
.plan-featured .plan-btn{width:104px;height:26px;line-height:26px}

/* footer */
.site-footer{left:0;top:1003px;width:727px;height:168px;background:var(--navy)}
.footer-col{top:1027px;color:var(--white)}
.footer-col h4{font-size:7.5px;font-weight:700;margin-bottom:9px;letter-spacing:.3px}
.footer-col p,.footer-col li{font-size:6px;line-height:13.5px}
.footer-col ul{list-style:none}
.quote{font-style:italic;width:135px;line-height:12px!important}
.author{display:flex;align-items:center;gap:13px;margin-top:10px}
.avatar{width:27px;height:27px;border-radius:50%;background:linear-gradient(#9fb3c8,#d7c4b0)}
.author small{display:block;font-style:italic;font-size:6px}
.t-arrows{left:186px;top:1027px;color:var(--white);font-size:8px;letter-spacing:4px}
.icon-line{display:flex;align-items:center;gap:7px;margin-top:3px}
.social{display:flex;align-items:center;gap:6px;margin-bottom:5px;font-size:6px}
.social-dot{width:16px;height:16px;border-radius:50%;background:var(--white)}
.badge{width:72px;height:28px;border-radius:3px;background:#4a6aa3;border:1px solid #7b93bd;margin-top:4px}
.footer-bottom{left:0;top:1171px;width:727px;height:29px;background:var(--navy-deep);color:var(--white);font-size:6px;text-align:center;line-height:29px}
</style>
</head>
<body>

<header class="site-header abs">
  <div class="brand abs">
    <span class="brand-mark"></span>
    <span class="brand-name">MRA<br>MERIDIAN RESCUE</span>
  </div>
  <div class="contact-bar abs">
    <div class="contact-item">
      <span class="contact-icon"><svg width="9" height="9" viewBox="0 0 24 24"><path fill="#fff" d="M6.6 10.8a15 15 0 0 0 6.6 6.6l2.2-2.2c.3-.3.7-.4 1-.2 1.1.4 2.3.6 3.6.6.6 0 1 .4 1 1V20c0 .6-.4 1-1 1A17 17 0 0 1 3 4c0-.6.4-1 1-1h3.5c.6 0 1 .4 1 1 0 1.3.2 2.5.6 3.6.1.3 0 .7-.2 1z"/></svg></span>
      <span>Call Us : 916-555-0187</span>
    </div>
    <div class="contact-item">
      <span class="contact-icon"><svg width="9" height="9" viewBox="0 0 24 24"><path fill="#fff" d="M2 5h20v14H2z"/><path fill="none" stroke="#2a8fd0" stroke-width="2" d="M2 5l10 8 10-8"/></svg></span>
      <span>Email Us : info@meridianrescue.com</span>
    </div>
  </div>
  <nav class="main-nav abs">
    <span>Home</span><span>Class Calender</span><span>Classes for Groups</span><span>Certification Classes</span><span>About Us</span><span>Policies</span>
  </nav>
</header>

<section class="hero abs" role="img" aria-label="Instructors guiding students practising CPR on a training manikin"></section>
<div class="hero-title abs">CPR+First Aid $59</div>
<div class="hero-sub abs">Adult/Child/Infant 3 hours or less!</div>
<div class="hero-arrows abs"><span class="hero-arrow"></span><span class="hero-arrow"></span></div>
<svg class="hero-curve abs" viewBox="0 0 727 40" preserveAspectRatio="none">
  <path d="M0 22 Q363 -4 727 22 L727 40 L0 40Z" fill="#fff"/>
  <path d="M0 22 Q363 -4 727 22" fill="none" stroke="#1b4a93" stroke-width="3"/>
</svg>

<div class="feature abs" style="left:62px"><div class="feature-photo" role="img" aria-label="Students seated in a weekly class" style="background:linear-gradient(#d8d4cc,#8a6a5a)"></div><div class="feature-label">WEEKLY CLASSES</div></div>
<div class="feature abs" style="left:216px"><div class="feature-photo" role="img" aria-label="Firefighter instructor demonstrating compressions" style="background:linear-gradient(#6a6a70,#2c2c34)"></div><div class="feature-label">LOCAL FIREFIGHTERS</div></div>
<div class="feature abs" style="left:370px"><div class="feature-photo" role="img" aria-label="Workers practising rescue on site" style="background:linear-gradient(#7a7d80,#3a3c40)"></div><div class="feature-label">SHORTER CLASSES</div></div>
<div class="feature abs" style="left:524px"><div class="feature-photo" role="img" aria-label="Training manikins in a classroom" style="background:linear-gradient(#a0a4ac,#d8b8b4)"></div><div class="feature-label">NO BOOK FEES</div></div>

<div class="feature-body abs" style="left:69px"><h3>ES SIMPLEMENTE EL TEXTO DE</h3><p>Es simplemente el texto de relleno de las imprentas y archivos de texto. Lorem Ipsum ha sido el texto</p></div>
<div class="feature-body abs" style="left:223px"><h3>ES SIMPLEMENTE EL TEXTO DE</h3><p>Es simplemente el texto de relleno de las imprentas y archivos de texto. Lorem Ipsum ha sido el texto</p></div>
<div class="feature-body abs" style="left:377px"><h3>ES SIMPLEMENTE EL TEXTO DE</h3><p>Es simplemente el texto de relleno de las imprentas y archivos de texto. Lorem Ipsum ha sido el texto</p></div>
<div class="feature-body abs" style="left:531px"><h3>ES SIMPLEMENTE EL TEXTO DE</h3><p>Es simplemente el texto de relleno de las imprentas y archivos de texto. Lorem Ipsum ha sido el texto</p></div>

<h1 class="welcome-title abs">WELCOME TO MERIDIAN RESCUE ACADEMY!</h1>
<p class="welcome-text abs">Meridian Rescue Academy is Northern California's leader in CPR, BLS, and Basic First Aid Certifications! Taught by experienced Firefighters, our classes are much shorter and provide common sense knowledge and skills to each student to help prepare them for actual emergencies.</p>

<div class="register register-online abs">
  <h2>REGISTER AND PAY ONLINE</h2>
  <p>REGISTERING/PAYING ONLINE WILL GUARANTEE YOUR SEAT IN CLASS AND YOU WILL RECEIVE YOUR CERTIFICATION THE DAY OF CLASS!</p>
  <div class="register-tab"><span>REGISTER</span></div>
</div>
<div class="register register-later abs">
  <h2>REGISTER ONLY AND PAY LATER</h2>
  <p>REGISTERING ONLY WILL NOT GUARANTEE YOUR SEAT IN CLASS AND YOUR CERTIFICATION WILL BE MAILED TO YOU WITHIN 1-2 BUSINESS DAYS.</p>
  <div class="register-tab"><span>REGISTER</span></div>
</div>

<section class="pricing abs"></section>
<div class="pricing-kicker abs">MRA PROFESSIONAL</div>
<div class="pricing-title abs">PRICING</div>
<div class="pricing-text abs">Meridian Rescue Academy is Northern California's leader in CPR, BLS, and Basic First Aid Certifications! Taught by experienced Fire-fighters, our classes are much shorter and provide common sense.<br><br>Knowledge and skills to each student to help prepare them for actual emergencies.</div>

<div class="plan abs" style="left:225px">
  <div class="plan-name">CPR</div>
  <div class="plan-price"><b>$39</b><span>Three Months</span></div>
  <div class="plan-row">Adult/Child/Infant</div><div class="plan-row alt">90 Minutes!</div><div class="plan-row">No Book Fees!</div>
  <div class="plan-btn">Sign Up</div>
</div>
<div class="plan abs" style="left:334px">
  <div class="plan-name">BLS</div>
  <div class="plan-price"><b>$49</b><span>Three Months</span></div>
  <div class="plan-row">Healthcare/Dental</div><div class="plan-row alt">90 Minutes!</div><div class="plan-row">No Book Fees!</div>
  <div class="plan-btn">Sign Up</div>
</div>
<div class="plan plan-featured abs" style="left:443px">
  <div class="plan-name">CPR+First Aid</div>
  <div class="plan-price"><b>$59</b><span>Three Months</span></div>
  <div class="plan-row">Adult/Child/Infant</div><div class="plan-row alt">3 hours or less!</div><div class="plan-row">No Book Fees!</div>
  <div class="plan-btn">Sign Up</div>
</div>
<div class="plan abs" style="left:563px">
  <div class="plan-name">BLS+First Aid</div>
  <div class="plan-price"><b>$69</b><span>Three Months</span></div>
  <div class="plan-row">Healthcare/Dental</div><div class="plan-row alt">90 Minutes!</div><div class="plan-row">No Book Fees!</div>
  <div class="plan-btn">Sign Up</div>
</div>

<footer class="site-footer abs"></footer>
<div class="footer-col abs" style="left:76px">
  <h4>TESTIMONIALS</h4>
  <p class="quote">Lorem Ipsum is simply dummy text of the printing and typesetting industry. Lorem Ipsum has been the industry's standard dummy text ever since</p>
  <div class="author"><span class="avatar" role="img" aria-label="Client portrait"></span><p>COLIN MARSH<small>Private Sector</small></p></div>
</div>
<div class="t-arrows abs">‹ ›</div>
<div class="footer-col abs" style="left:252px">
  <h4>WELCOME</h4>
  <ul><li>Class Calender</li><li>Certification Classes</li><li>Classes for Groups</li><li>About Us</li><li>Policies</li><li>Medesto</li><li>Manteca/Tracy</li><li>Livermore</li></ul>
</div>
<div class="footer-col abs" style="left:377px">
  <h4>CONTACT INFO</h4>
  <p>MRA PROFESSIONAL</p>
  <p style="line-height:15px">120 Street Name, State name,<br>Country name, Zip code : 2350 3652.</p>
  <p class="icon-line"><svg width="6" height="8" viewBox="0 0 6 8"><rect x=".5" y=".5" width="5" height="7" rx="1" fill="none" stroke="#fff"/></svg>916-555-0187</p>
  <p class="icon-line"><svg width="8" height="6" viewBox="0 0 8 6"><rect width="8" height="6" fill="#fff"/><path d="M0 0l4 3 4-3" fill="none" stroke="#143a7a"/></svg>info@meridianrescue.com</p>
</div>
<div class="footer-col abs" style="left:544px">
  <h4>CONTACT INFO</h4>
  <div class="social"><span class="social-dot"></span>: Friendwall</div>
  <div class="social"><span class="social-dot"></span>: Circlepost</div>
  <div class="social"><span class="social-dot"></span>: Chirpline</div>
  <div class="badge"></div>
</div>
<div class="footer-bottom abs">Copyright © 2015 Meridian Rescue Academy. All rights reserved.</div>

</body>
</html>
```